Business Performance Improvement Book Cover Design Project

We need a book cover design for a new company, based in Eastern Australia, called Brovanta Consulting. We advise clients on process improvement, continuous improvement and business performance improvement, especially in the manufacturing areas and Fast Moving Consumer Goods industries.
We have a written a book designed to demonstrate our very high calibre of knowledge and to use as a marketing tool for prospective clients. We hope to give it out at training seminars and as a comprehensive business card.

Title of the book is: A rounded method for Enterprise Results Advancement.
Subtitle: Shape a Steady Refinement method to fit your firm's character.
Author: by Gareth Polwyn
Back Cover: No need for a bar code in this edition. An important aspect is that we will distribute by hand. Text below for back page.

'For the experienced Business Performers, this book is designed to offer an insight into the advantages and an example of an approach to Business Improvement. It is not the only way but it is tried and tested in world class companies and it works. For those new to Continuous Improvement, it offers a helpful introduction to a holistic business improvement system, an overview of important success factors and pitfalls, recommendations on how to implement tools and methods and a quick guide to see when to use which tools. '

'Consultancies are one of many tools management teams can engage and management must make sure the consultants tailor their approach to suit its business needs and culture and not vice versa.'

End of text for back cover.

Business Performance Improvement is also known as or can include:
Continuous Improvement
Process Improvement
Lean Six Sigma
Operational Excellence
Total Productive Maintenance
Varmeco Output Method
Total Quality Management
Business Process Re engineering
Yield Compass
=
Brovanta Consulting

The book size is 175 x 240 mm and will need a 10-15mm bleed. The spine is not known at this stage exactly and will need to be updated once the printing is finished but I suggest a 10mm until I have the exact size.

Our company colours are Pantone 288, R0,G75,B141, C100,M79,Y17,K3. Attached are some other publications that give a sense of what we like to portray, Some words which might add to this are: professional, elegance, quality, sleek.
Updates

Reason: After receiving the designs, I realised that I needed to update the brief with more and better quality information for designers to work with.

Target Market(s)

people in the accounting and insolvency industries, production managers and CEOs, Chief Operating Officers, members of the executive team of large companies and GMs of small companies.

Industry/Entity Type

Marketing

Requirements
Must have
• Communicate an image that shows an improvement or increase of something.
Very professional and elegant
Emphasis on the words 'Business Performance Improvement' in the title, subtitle also important
Must appeal to a high-end of the market audience
Nice to have
• Recommendation for your cover to be gloss or matt in print
Image can be indirectly related to money but not specifically
Somehow that it matches or is not so different to the attached brochure
Should not have
• Not be too loud or commercial
Book jacket. WIll be printed as soft cover first run and hard cover 2nd run

```html
<!DOCTYPE html>
<html lang="en">
<head>
<meta charset="utf-8">
<title>A Rounded Method for Enterprise Results Advancement</title>
<link rel="stylesheet" href="https://fonts.googleapis.com/css2?family=Noto+Serif:wdth,wght@87.5,400&display=swap">
<style>
  :root {
    --paper: #f7f8fb;
    --mist: #dfe3ec;
    --haze: #b9c1d2;
    --ornament-blue: #5d7ea8;
    --ornament-deep: #3f5f8a;
    --ink: #111111;
    --shadow: rgba(0, 0, 0, 0.55);
  }
  html, body {
    margin: 0;
    padding: 0;
    width: 846px;
    height: 1200px;
    overflow: hidden;
    background: var(--paper);
  }
  .cover {
    position: relative;
    width: 846px;
    height: 1200px;
    overflow: hidden;
    font-family: "Noto Serif", "DejaVu Serif", serif;
    font-stretch: 87.5%;
    color: var(--ink);
  }
  .cover__backdrop {
    position: absolute;
    inset: 0;
    background:
      radial-gradient(ellipse 520px 300px at 380px 360px, rgba(185,193,210,0.55), transparent 70%),
      radial-gradient(ellipse 480px 260px at 520px 900px, rgba(185,193,210,0.5), transparent 70%),
      radial-gradient(ellipse 360px 220px at 720px 700px, rgba(223,227,236,0.9), transparent 70%),
      linear-gradient(160deg, #ffffff 0%, var(--paper) 45%, var(--mist) 100%);
  }
  .cover__ornament {
    position: absolute;
  }
  .cover__ornament--top {
    left: 0;
    top: 0;
    width: 180px;
    height: 230px;
    background: radial-gradient(ellipse at 20% 30%, var(--ornament-deep), var(--ornament-blue) 45%, rgba(93,126,168,0) 75%);
    opacity: 0.85;
  }
  .cover__ornament--bottom {
    left: 0;
    top: 780px;
    width: 240px;
    height: 420px;
    background: radial-gradient(ellipse 80% 70% at 15% 60%, var(--ornament-deep), var(--ornament-blue) 50%, rgba(93,126,168,0) 80%);
    opacity: 0.85;
  }
  .cover__title,
  .cover__subtitle,
  .cover__author {
    position: absolute;
    right: 44px;
    margin: 0;
    text-align: right;
    font-weight: 400;
    text-shadow: 3px 3px 3px var(--shadow);
  }
  .cover__title {
    top: 58px;
    font-size: 77px;
    line-height: 88px;
  }
  .cover__subtitle {
    top: 596px;
    font-size: 34px;
    line-height: 48px;
    text-shadow: 2px 2px 2px rgba(0,0,0,0.4);
  }
  .cover__author {
    top: 1102px;
    font-size: 31px;
    line-height: 40px;
    text-shadow: 2px 2px 2px rgba(0,0,0,0.45);
  }
  .line { display: block; }
</style>
</head>
<body>
  <main class="cover">
    <div class="cover__backdrop" role="img" aria-label="Soft abstract pattern of pale grey and white swept shapes"></div>
    <div class="cover__ornament cover__ornament--top" role="img" aria-label="Blue flourish ornament with curling scrolls"></div>
    <div class="cover__ornament cover__ornament--bottom" role="img" aria-label="Blue flourish ornament with scrolls and leaf shapes"></div>

    <h1 class="cover__title">
      <span class="line">A Rounded</span>
      <span class="line">Method</span>
      <span class="line">For Enterprise</span>
      <span class="line">Results</span>
      <span class="line">Advancement</span>
    </h1>

    <p class="cover__subtitle">
      <span class="line">Shape a</span>
      <span class="line">Steady Refinement</span>
      <span class="line">method to fit your firm's</span>
      <span class="line">character.</span>
    </p>

    <p class="cover__author">Gareth Polwyn B. Mech Eng., M. Sc (KVT)</p>
  </main>
</body>
</html>
```